Brightway Haul & Upkeep Services, are a company that offers a 'one stop shop' pre-move clean up a

I have already selected a logo which I would like on the front of the business cards along with phone numbers, web address and email which are:
0487650392
www.brightwayhaul.com.au
brightwayhaulandupkeep@mailbox.example

On the back of the card I would like to list some of the types of service we offer (clean - move - repairs/maintenance) which are:
CLEAN - windows, gutters, solar panels, driveways/paths, carpets.
MOVE - Small/medium size house/office moves, large item pick-up & delivery, yard clean-up and removal.
General maintenance and repairs.

I would like the blue logo on a gray background.

Thanks

```html
<!DOCTYPE html>
<html lang="en">
<head>
<meta charset="utf-8">
<title>Brightway Haul &amp; Upkeep Services – Business Card</title>
<link href="https://fonts.googleapis.com/css2?family=Open+Sans:wght@400;600;700&display=swap" rel="stylesheet">
<style>
  :root {
    --backdrop: #e7e4df;
    --silver-light: #f1f1f2;
    --silver-mid: #d9dadc;
    --silver-dark: #b9bbbe;
    --brand-blue: #2f6db5;
    --ink: #262626;
    --swoosh: #1c1c1c;
    --white: #ffffff;
  }
  * { box-sizing: border-box; margin: 0; padding: 0; }
  html, body {
    width: 1200px; height: 373px; overflow: hidden;
    background: var(--backdrop);
    font-family: "Open Sans", Arial, sans-serif;
  }
  .card {
    position: absolute;
    top: 30px;
    width: 546px; height: 312px;
    border-radius: 22px;
    overflow: hidden;
    background: radial-gradient(ellipse at 50% 35%, var(--silver-light) 0%, var(--silver-mid) 60%, var(--silver-dark) 100%);
    box-shadow: 0 0 0 1px rgba(0,0,0,0.25);
  }
  .card--front { left: 37px; }
  .card--back { left: 622px; }

  .brand-name {
    position: absolute;
    left: 0; right: 0;
    text-align: center;
    color: var(--brand-blue);
    font-weight: 700;
    text-transform: uppercase;
    line-height: 1.12;
  }
  .card--front .brand-name { top: 86px; left: 60px; right: 120px; font-size: 27px; }
  .card--back .brand-name { top: 92px; font-size: 27px; }

  .contact-list {
    position: absolute;
    left: 78px; top: 194px;
    list-style: none;
    font-size: 15px;
    color: var(--ink);
  }
  .contact-list li { display: flex; align-items: center; height: 22px; }
  .contact-list svg { width: 10px; height: 10px; margin-right: 8px; }

  .wave { position: absolute; left: 0; bottom: 0; width: 546px; height: 312px; }

  .phone {
    position: absolute;
    right: 20px; bottom: 18px;
    color: var(--white);
    font-size: 18px;
    display: flex; align-items: center; gap: 6px;
  }
  .phone svg { width: 14px; height: 14px; }

  .services-title {
    position: absolute;
    top: 187px; left: 0; right: 0;
    text-align: center;
    color: var(--brand-blue);
    font-size: 22px; font-weight: 600;
    letter-spacing: 2px;
  }
  .services-list {
    position: absolute;
    top: 232px; left: 0; right: 0;
    text-align: center;
    font-size: 15px; font-weight: 600;
    color: var(--ink);
    line-height: 27px;
  }
  .services-list span { margin: 0 6px; }
  .services-list .bullet { color: var(--brand-blue); margin: 0 3px 0 0; }
</style>
</head>
<body>
  <section class="card card--front">
    <svg class="wave" viewBox="0 0 546 312" aria-hidden="true">
      <path d="M0,195 C70,232 150,282 250,292 C160,290 80,250 0,222 Z" fill="var(--swoosh)"/>
      <path d="M0,232 C90,262 170,300 270,292 C360,284 430,232 546,218 L546,312 L0,312 Z" fill="var(--brand-blue)"/>
    </svg>
    <p class="brand-name">Brightway Haul<br>&amp; Upkeep Services</p>
    <ul class="contact-list">
      <li>
        <svg viewBox="0 0 10 10" aria-hidden="true"><rect x="0.5" y="2" width="9" height="6.5" rx="1" fill="var(--brand-blue)"/><path d="M0.8,2.5 L5,5.8 L9.2,2.5" stroke="#fff" stroke-width="0.9" fill="none"/></svg>
        brightwayhaulandupkeep@mailbox.example
      </li>
      <li>
        <svg viewBox="0 0 10 10" aria-hidden="true"><circle cx="5" cy="5" r="4.5" fill="var(--brand-blue)"/><path d="M0.5,5 H9.5 M5,0.5 C2.5,3 2.5,7 5,9.5 M5,0.5 C7.5,3 7.5,7 5,9.5" stroke="#fff" stroke-width="0.7" fill="none"/></svg>
        www.brightwayhaul.com.au
      </li>
    </ul>
    <p class="phone">
      <svg viewBox="0 0 14 14" aria-hidden="true"><path d="M3,1 L5,1 L6,4 L4.5,5.2 C5.3,7 7,8.7 8.8,9.5 L10,8 L13,9 L13,11 C13,12 12,13 11,13 C5.5,12.5 1.5,8.5 1,3 C1,2 2,1 3,1 Z" fill="var(--white)"/></svg>
      0487650392
    </p>
  </section>

  <section class="card card--back">
    <p class="brand-name">Brightway Haul<br>&amp; Upkeep Services</p>
    <h2 class="services-title">Services we offer</h2>
    <div class="services-list">
      <p><span><b class="bullet">•</b>Clean</span><span><b class="bullet">•</b>Move</span></p>
      <p><span><b class="bullet">•</b>General Maintenance And Repairs.</span></p>
    </div>
  </section>
</body>
</html>
```